Brightfield Ventures Inc. Letterhead

Creation of attractive and eye catching letterhead for a business start-up for the construction industry. Letterhead must relate to construction, but avoid standard hammer and tools in the design.

I forgot to add some details, sorry about that. Some pertinent info: Ph: 916-555-0187 brightfieldventures.example 448 Willowmere Ave, Ste 210 Folsom, CA 95999 info@brightfieldventures.example not sure if slogan should be in there" “Connecting construction professionals to create a purpose driven industry.” must be able to be used in word. Thanks!

```html
<!DOCTYPE html>
<html lang="en">
<head>
<meta charset="utf-8">
<title>Brightfield Ventures Inc. Letterhead</title>
<link rel="stylesheet" href="https://fonts.googleapis.com/css2?family=Open+Sans:wght@400;600;700&family=Arimo:wght@700&display=swap">
<style>
  :root {
    --backdrop: #e4e5e7;
    --paper: #ffffff;
    --brand-red: #c0161c;
    --brand-navy: #1b2a5c;
    --ink: #2b2b2b;
    --ink-soft: #555a60;
  }
  * { margin: 0; padding: 0; box-sizing: border-box; }
  html, body { width: 1200px; height: 945px; overflow: hidden; }
  body {
    background: var(--backdrop);
    display: flex; align-items: center; justify-content: center;
    font-family: "Open Sans", sans-serif;
  }
  .letterhead {
    position: relative;
    width: 640px; height: 905px;
    background: var(--paper);
    box-shadow: 0 6px 24px rgba(0,0,0,0.12);
    overflow: hidden;
  }
  .contact-list {
    position: absolute; top: 52px; right: 58px;
    list-style: none; font-size: 9px; color: var(--ink-soft); line-height: 1.45;
  }
  .contact-list li { display: flex; align-items: center; gap: 6px; }
  .contact-list svg { width: 8px; height: 8px; fill: var(--brand-red); flex: none; }
  .brand {
    position: absolute; top: 96px; left: 58px;
    display: flex; align-items: center; gap: 8px;
  }
  .brand-mark { width: 14px; height: 14px; background: var(--brand-red); }
  .brand-name {
    font-weight: 700; font-size: 17px; letter-spacing: 0.5px; color: var(--brand-navy);
  }
  .brand-rule {
    position: absolute; top: 126px; left: 58px; width: 212px; height: 1.5px;
    background: var(--brand-red);
  }
  .salutation {
    position: absolute; top: 232px; left: 74px;
    font-family: "Arimo", sans-serif; font-weight: 700; font-size: 15px; color: #4a4a4a;
  }
  .letter-body {
    position: absolute; top: 272px; left: 74px; width: 500px;
    font-size: 12.5px; line-height: 1.42; color: var(--ink);
  }
  .letter-body p + p { margin-top: 18px; }
  .signature {
    position: absolute; top: 690px; left: 110px; width: 140px; height: 48px;
    background: linear-gradient(90deg, #d9d9d9, #efefef); border-radius: 4px;
  }
  .footer-band { position: absolute; left: 0; bottom: 0; width: 640px; height: 56px; }
  .footer-address {
    position: absolute; bottom: 14px; left: 0; width: 640px; text-align: center;
    font-size: 10.5px; color: #fff;
  }
</style>
</head>
<body>
  <main class="letterhead">
    <ul class="contact-list">
      <li><svg viewBox="0 0 10 10"><path d="M2 0.5l2 2-1 1.2c.7 1.4 1.8 2.5 3.2 3.2l1.2-1 2 2-1.4 1.6C4.5 9.5.5 5.5.4 2z"/></svg>Ph: 916-555-0187</li>
      <li><svg viewBox="0 0 10 10"><path d="M0 2h10v6H0zM0 2l5 3.5L10 2" /></svg>info@brightfieldventures.example</li>
      <li><svg viewBox="0 0 10 10"><circle cx="5" cy="5" r="4.5"/></svg>brightfieldventures.example</li>
    </ul>

    <div class="brand">
      <span class="brand-mark"></span>
      <span class="brand-name">Brightfield Ventures Inc.</span>
    </div>
    <div class="brand-rule"></div>

    <p class="salutation">Dear Mr. Dalton,</p>

    <section class="letter-body">
      <p>Lorem Ipsum is simply dummy text of the printing and typesetting industry. Lorem Ipsum has been the industry's standard dummy text ever since the 1500s, when an unknown printer took a galley of type and scrambled it to make a type specimen book. It has survived not only five centuries, but also the leap into electronic typesetting, remaining essentially unchanged.</p>
      <p>The standard chunk of Lorem Ipsum used since the 1500s is reproduced below for those interested. Sections 1.10.32 and 1.10.33 from "de Finibus Bonorum et Malorum" by Aurelio are also reproduced in their exact original form, accompanied by English versions from the 1914 translation by H.Marlow.</p>
      <p>Lorem Ipsum is simply dummy text of the printing and typesetting industry. Lorem Ipsum has been the industry's standard dummy text ever since the 1500s, when an unknown printer took a galley of type and scrambled it to make a type specimen book. It has survived not only five centuries, but also the leap into electronic typesetting, remaining essentially unchanged. It was popularised in the</p>
      <p>Lorem Ipsum is simply dummy text of the printing and typesetting industry. Lorem Ipsum has been the industry's standard dummy text ever since the 1500s, when an unknown printer took a galley of type and scrambled it to make a type specimen book.</p>
    </section>

    <div class="signature" role="img" aria-label="Handwritten signature"></div>

    <svg class="footer-band" viewBox="0 0 640 56" preserveAspectRatio="none" aria-hidden="true">
      <rect x="0" y="42" width="640" height="14" fill="var(--brand-red)"/>
      <rect x="0" y="30" width="640" height="6" fill="var(--brand-navy)"/>
      <path d="M150 56 V30 Q150 16 166 16 H474 Q490 16 490 30 V56 Z" fill="#fff"/>
      <path d="M156 56 V32 Q156 21 170 21 H470 Q484 21 484 32 V56 Z" fill="var(--brand-red)"/>
    </svg>
    <p class="footer-address">448 Willowmere Ave, Ste 210, Folsom, CA 95999</p>
  </main>
</body>
</html>
```